I need to make a car magnet

It needs to include the words "PLAVO TOUR" and "2026 MEMBER" as well as the attached silhouette of the golfer. The color scheme needs to be navy, red and white. The shape and dimensions are open for interpretation

```html
<!DOCTYPE html>
<html lang="en">
<head>
<meta charset="UTF-8">
<title>PLAVO TOUR – 2026 Member Car Magnet</title>
<link rel="stylesheet" href="https://fonts.googleapis.com/css2?family=Russo+One&display=swap">
<style>
  :root {
    --navy: #1e2c5c;
    --red: #e42532;
    --white: #ffffff;
    --backdrop: #b2b2b2;
  }
  * { margin: 0; padding: 0; box-sizing: border-box; }
  html, body {
    width: 892px;
    height: 1200px;
    overflow: hidden;
    background: var(--backdrop);
  }
  .magnet {
    position: absolute;
    left: 60px;
    top: 407px;
    width: 772px;
    height: 386px;
    background: var(--white);
    box-shadow: 2px 3px 5px rgba(0, 0, 0, 0.25);
    overflow: hidden;
  }
  .identity {
    position: absolute;
    left: 48px;
    top: 44px;
    width: 440px;
    display: flex;
    flex-direction: column;
    align-items: center;
  }
  .name {
    font-family: "Russo One", sans-serif;
    font-weight: 400;
    font-size: 92px;
    line-height: 0.98;
    color: var(--navy);
    text-align: center;
    white-space: nowrap;
  }
  .member-tag {
    margin-top: 26px;
    padding: 9px 30px;
    background: var(--red);
    border-radius: 4px;
  }
  .member-tag__text {
    display: block;
    font-family: "Russo One", sans-serif;
    font-size: 30px;
    line-height: 1;
    letter-spacing: 1px;
    color: var(--white);
    white-space: nowrap;
  }
  .golfer {
    position: absolute;
    left: 530px;
    top: 12px;
    width: 210px;
    height: 352px;
    background: linear-gradient(180deg, #24356b 0%, var(--navy) 100%);
    border-radius: 8px;
  }
  .turf {
    position: absolute;
    left: 0;
    bottom: 0;
    width: 100%;
    height: 34px;
    background: var(--navy);
  }
</style>
</head>
<body>
  <div class="magnet">
    <div class="identity">
      <div class="name">PLAVO<br>TOUR</div>
      <div class="member-tag"><span class="member-tag__text">2026 MEMBER</span></div>
    </div>
    <div class="golfer" role="img" aria-label="Navy silhouette of a golfer putting a ball"></div>
    <div class="turf" role="img" aria-label="Navy grass strip along the bottom edge"></div>
  </div>
</body>
</html>
```